4th Generation Family Business Needs a New Card Design!

We are a family owned 4th Generation company. We are based in the Sydney, Australia area and we are desperately in need of a more modern and classy card. We are monumental masons who design, supply & erect lasting memorials throughout cemeteries in Sydney. Our customers are normally in a period of grieving. I have attached logo files that will need to be implemented on the card. Company was established 1935. Australian Owned and Operated. Card needs to be designed to PIXO.com specification.

Target Market(s)

Our target market is based upon people that a grieving for family members that have passed away. We also deal with alot of companies that own and operate cemeteries.

Industry/Entity Type

Business

Contact Information for Business Card

Simon Harcourt, Operations Manager, 0417293086, simon@harcourtmemorials.com.au
Lewis Harcourt, Director, 0491630572, lewis@harcourtmemorials.com.au
Phone # 02 9561 3048
Website: www.harcourtmemorials.com.au
Address: Suite 17, 8 Palfrey Lane, West Carlow, Sydney NSW 2156

Font styles to use
Serif
Decorative
Script

Requirements
Must have
• Would like to see the logo nicely implemented with a modern design. Embossed lettering would be a nice additive.

```html
<!DOCTYPE html>
<html lang="en">
<head>
<meta charset="utf-8">
<title>Harcourt Memorials – Business Card</title>
<link rel="stylesheet" href="https://fonts.googleapis.com/css2?family=Cinzel:wght@400;600&family=Roboto+Slab:wght@300&display=swap">
<style>
  :root {
    --backdrop: #e4e4e2;
    --card-black: #0b0b0c;
    --card-sheen: #2c2c2e;
    --gold: #d8ad2a;
    --gold-light: #ecc94a;
    --white: #f4f4f2;
    --silver: #b9b9bb;
    --text-soft: #dcdcdc;
  }
  * { margin: 0; padding: 0; box-sizing: border-box; }
  html, body { width: 1200px; height: 576px; overflow: hidden; background: var(--backdrop); }
  .canvas { position: relative; width: 1200px; height: 576px; }

  .card {
    position: absolute;
    background:
      radial-gradient(ellipse 90px 240px at 40% 45%, rgba(90,90,94,.55), transparent 70%),
      var(--card-black);
    box-shadow: 0 2px 5px rgba(0,0,0,.35);
    overflow: hidden;
  }
  .card--front { left: 81px; top: 138px; width: 485px; height: 294px; }
  .card--back  { left: 602px; top: 138px; width: 481px; height: 292px;
    background:
      radial-gradient(ellipse 80px 230px at 36% 40%, rgba(90,90,94,.5), transparent 70%),
      var(--card-black); }

  .wordmark { position: absolute; text-align: center; font-family: "Cinzel", serif; font-weight: 400; color: var(--white); line-height: 1; }
  .wordmark__badge { display: block; margin: 0 auto 10px; border: 3px solid var(--white); }
  .wordmark__name { display: block; letter-spacing: 1px; }
  .wordmark__sub { display: block; letter-spacing: 2px; margin-top: 4px; }

  .card--front .wordmark { left: 0; width: 100%; top: 78px; }
  .card--front .wordmark__badge { width: 62px; height: 62px; }
  .card--front .wordmark__name { font-size: 38px; }
  .card--front .wordmark__sub { font-size: 15px; }

  .card--back .wordmark { left: 22px; width: 158px; top: 24px; }
  .card--back .wordmark__badge { width: 50px; height: 50px; margin-bottom: 8px; }
  .card--back .wordmark__name { font-size: 29px; }
  .card--back .wordmark__sub { font-size: 12px; }

  .front-band { position: absolute; left: 0; bottom: 0; width: 100%; height: 11px; background: linear-gradient(90deg, var(--gold), var(--gold-light) 40%, var(--gold)); }

  .faint-square { position: absolute; right: -30px; top: 40px; width: 170px; height: 170px; border: 4px solid rgba(255,255,255,.06); background: rgba(255,255,255,.02); }

  .rule { position: absolute; left: 24px; top: 171px; width: 236px; height: 1px; background: var(--gold); }

  .person { position: absolute; right: 23px; top: 160px; text-align: right; }
  .person__name { font-family: "Cinzel", serif; font-weight: 600; font-size: 21px; color: var(--white); line-height: 1; letter-spacing: .5px; }
  .person__title { font-family: "Roboto Slab", serif; font-weight: 300; font-size: 12px; color: var(--text-soft); margin-top: 4px; }
  .address { position: absolute; right: 23px; top: 208px; text-align: right; font-family: "Roboto Slab", serif; font-weight: 300; font-size: 13px; line-height: 19px; color: var(--text-soft); }

  .contacts { position: absolute; left: 26px; top: 191px; list-style: none; font-family: "Roboto Slab", serif; font-weight: 300; font-size: 13px; color: var(--text-soft); }
  .contacts li { display: flex; align-items: center; height: 17.5px; }
  .contacts svg { width: 10px; height: 10px; margin-right: 10px; fill: var(--gold); flex: none; }

  .band-silver { position: absolute; left: 0; bottom: 0; width: 100%; height: 12px; background: linear-gradient(90deg, #8d8d8f, var(--silver) 40%, #9a9a9c); }
  .band-gold { position: absolute; right: 0; bottom: 0; width: 250px; height: 27px; background: linear-gradient(90deg, var(--gold-light), var(--gold)); clip-path: polygon(18px 0, 100% 0, 100% 100%, 0 100%); }
</style>
</head>
<body>
<main class="canvas">

  <section class="card card--front" aria-label="Card front">
    <div class="wordmark">
      <span class="wordmark__badge"></span>
      <span class="wordmark__name">HARCOURT</span>
      <span class="wordmark__sub">MEMORIALS</span>
    </div>
    <div class="front-band"></div>
  </section>

  <section class="card card--back" aria-label="Card back">
    <div class="faint-square"></div>
    <div class="wordmark">
      <span class="wordmark__badge"></span>
      <span class="wordmark__name">HARCOURT</span>
      <span class="wordmark__sub">MEMORIALS</span>
    </div>

    <div class="rule"></div>

    <div class="person">
      <p class="person__name">SIMON HARCOURT</p>
      <p class="person__title">Operations Manager</p>
    </div>

    <address class="address" style="font-style:normal">
      Suite 17, 8 Palfrey Lane,<br>
      West Carlow, Sydney NSW 2156
    </address>

    <ul class="contacts">
      <li><svg viewBox="0 0 10 10"><path d="M2 0.5l2 2-1 1.2c.6 1.3 1.6 2.3 2.8 2.8l1.2-1 2 2-1.3 1.8C4 9.5 .5 6 .3 1.8z"/></svg>0491630572</li>
      <li><svg viewBox="0 0 10 10"><path d="M0 3c2-2 8-2 10 0v1.5H7.5V3.3h-5v1.2H0zM2 5h6l1.5 4h-9z"/></svg>02 9561 3048</li>
      <li><svg viewBox="0 0 10 10"><path d="M0 2h10v6H0zM1 3v.3l4 2.6 4-2.6V3z" fill-rule="evenodd"/></svg>harcourtmemorials.com.au</li>
      <li><svg viewBox="0 0 10 10"><circle cx="5" cy="5" r="4.5" fill="none" stroke="#d8ad2a" stroke-width="1"/><path d="M0.5 5h9M5 .5v9" stroke="#d8ad2a" stroke-width=".8"/></svg>lewis@harcourtmemorials.com.au</li>
    </ul>

    <div class="band-silver"></div>
    <div class="band-gold"></div>
  </section>

</main>
</body>
</html>
```